Business Card Design For A Cajun Seafood Restaurant

We are opening a cajun seafood restaurant in a week. We mainly serve cajun seafood which is orginally from Louisiana. We want design on both sides of a business card. I have menu on the website. You can go to www.reednkettle.example to check out our menu.

Restaurant name: Reed N' Kettle
Phone: +1 (555) 304-7712
Address: 48206 Ludlow Row, #7, Bexmoor Flats, Ca90000
Email: reednkettle@mailbox.example
Website: www.reednkettle.example

Maybe add social media icons (facebook, instagram) if looks nice on the business card.
facebook.com/reednkettle
instagram.com/reednkettle or @reednkettle

Attached is the logo and other business card samples that I like.

```html
<!DOCTYPE html>
<html lang="en">
<head>
<meta charset="utf-8">
<title>Reed N' Kettle – Business Card</title>
<link href="https://fonts.googleapis.com/css2?family=Source+Sans+3:wght@400;600&display=swap" rel="stylesheet">
<style>
  :root{
    --stage:#3b3b3b;
    --paper:#fbfbfb;
    --ink:#0a0a0a;
    --orange:#ff6a00;
    --amber:#ffc400;
    --white:#ffffff;
    --text-dark:#1e1e1e;
    --crab-a:#f47a20;
    --crab-b:#f2b534;
  }
  *{margin:0;padding:0;box-sizing:border-box}
  html,body{width:1200px;height:750px;overflow:hidden}
  body{background:var(--stage);font-family:"Source Sans 3",sans-serif;position:relative}

  .card{position:absolute;top:228px;width:461px;height:262px;border-radius:12px;overflow:hidden;background:var(--paper)}
  .card--front{left:124px}
  .card--back{left:618px}

  .card__shape{position:absolute;inset:0}

  .mascot{position:absolute;border-radius:40%;background:radial-gradient(circle at 50% 45%,var(--crab-b) 0%,var(--crab-a) 60%,rgba(244,122,32,0) 72%)}
  .card--front .mascot{left:92px;top:72px;width:86px;height:66px}
  .card--back .mascot{left:146px;top:48px;width:170px;height:164px}

  .brand{position:absolute;left:36px;top:152px;width:186px;display:flex;align-items:center;justify-content:center;gap:7px}
  .brand__dot{width:10px;height:10px;border-radius:50%;background:var(--orange)}
  .brand__name{font-size:19px;font-weight:600;color:var(--ink);letter-spacing:.5px}

  .person{position:absolute;right:25px;top:30px;text-align:right}
  .person__name{font-size:18px;font-weight:600;color:var(--orange);line-height:1.2}
  .person__role{font-size:13px;color:var(--amber);line-height:1.2}

  .contact{position:absolute;right:25px;top:143px;text-align:right;color:var(--white);font-size:12.5px;line-height:17px}
  .contact__address{margin-bottom:7px}
  .contact__line{display:flex;justify-content:flex-end;align-items:center;gap:6px}
  .contact__icon{width:11px;height:11px;flex:none}

  .social{position:absolute;left:0;right:0;top:221px;display:flex;justify-content:center;gap:4px;font-size:13px;color:var(--text-dark)}
  .social__item{display:flex;align-items:center;gap:3px}
  .social__dot{width:16px;height:16px;border-radius:50%;background:var(--orange)}
</style>
</head>
<body>

<section class="card card--front">
  <svg class="card__shape" viewBox="0 0 461 262" aria-hidden="true">
    <path d="M218 0 Q268 90 258 160 Q262 70 236 0 Z" fill="var(--amber)"/>
    <path d="M234 0 Q292 131 210 262 L461 262 L461 0 Z" fill="var(--orange)"/>
    <path d="M244 0 Q296 131 222 262 L461 262 L461 0 Z" fill="var(--ink)"/>
  </svg>

  <div class="mascot" role="img" aria-label="Illustrated crab mascot holding a corn cob"></div>
  <div class="brand">
    <span class="brand__dot"></span>
    <span class="brand__name">REED N' KETTLE</span>
  </div>

  <div class="person">
    <div class="person__name">DALE MERCER</div>
    <div class="person__role">CEO/Founder</div>
  </div>

  <div class="contact">
    <div class="contact__address">48206 Ludlow Row, #7<br>Bexmoor Flats, Ca90000</div>
    <div class="contact__line">+1 (555) 304-7712
      <svg class="contact__icon" viewBox="0 0 12 12"><path d="M2.5 1 L4.5 1 L5.2 3.6 L4 4.6 Q5 7 7.4 8 L8.4 6.8 L11 7.5 L11 9.5 Q10.5 11 9 11 Q1 10 1 2.5 Q1 1 2.5 1Z" fill="var(--orange)"/></svg>
    </div>
    <div class="contact__line">reednkettle@mailbox.example
      <svg class="contact__icon" viewBox="0 0 12 12"><rect x="0.5" y="2.5" width="11" height="7.5" fill="var(--orange)"/><path d="M0.5 2.5 L6 6.8 L11.5 2.5" stroke="var(--ink)" stroke-width="1" fill="none"/></svg>
    </div>
    <div class="contact__line">www.reednkettle.example
      <svg class="contact__icon" viewBox="0 0 12 12"><circle cx="6" cy="6" r="5.5" fill="var(--orange)"/><path d="M3 3.5 Q5 4 4.5 6 Q6 7 5 9.5 M7.5 2 Q7 4 9 5" stroke="var(--ink)" stroke-width="1" fill="none"/></svg>
    </div>
  </div>
</section>

<section class="card card--back">
  <div class="mascot" role="img" aria-label="Large illustrated crab mascot holding a corn cob overhead"></div>
  <div class="social">
    <span class="social__item"><span class="social__dot"></span>reednkettle</span>
    <span class="social__item"><span class="social__dot"></span>@reednkettle</span>
  </div>
</section>

</body>
</html>
```